Plenko - Shoe Fitting App : Foot scanning app, 3D reconstruction and Fit recommandation.

We are a startup that has developed a 3D scanning App that compares the 3d reconstructed foot to the 3D Last (mould) of a shoe to find the best match and recommend a shoe size with a graphical representation of the fit on a reconstructed foot without texturing. The challenge of this app is to have a simple and intuitive onboarding of the user with clean and crisp ui and a simple tutorial for foot scanning. 3D representation of the fit is also key. What you see is what you feel is what we would like to achieve.

Target Market(s)

Sneaker Brands and athletic shoes brands

Industry/Entity Type

Footwear

Font styles to use
Other font styles liked:
• Oswald or Droid Serif

Colors
0094D4
00A9DD
6FCCEA
C7EBF8
E9F6FB

Requirements
Must have
• Simple intuitive UI to onboard the customer to scan his bare foot (please look at attached image on how to scan the foot). You must flip your phone so that the screen is facing your foot. Start at 40cm distance form the front of your foot and turn 360% slowly to capture the foot while you feel the aptic of the Phone. That needs to be presented with a simple animation that the user can easily understand and skip if he is a returning customer and knows how to do that. the rest of the UI is to present the result of the scanned foot for the user to use to get his fit and size. The other must have is the final result screen. Where the user will a representation of the foot (snug, loose ) of different predefined areas of the foot so he can choose the fit that he likes and not necessarily the size that we suggest. Must match website design (https://www.plenko.example)
Nice to have
• An animation of the whole process (scan-compare 3d foot with 3d shoe last(or mould) and get the 3D result of the best fit + associated size. Optionaly, an option to play with your foot and transform it (avatar like with accessories and colours)
Should not have
• Too many colours. Too much text. No gender type. No race type.

```html
<!DOCTYPE html>
<html lang="en">
<head>
<meta charset="utf-8">
<title>Plenko — Onboarding</title>
<link rel="stylesheet" href="https://fonts.googleapis.com/css2?family=Montserrat:wght@800&family=Oswald:wght@500;600&family=Raleway:wght@400;500;700;800&display=swap">
<style>
  :root {
    --teal: #4aa9b0;
    --violet: #5a4f9e;
    --deep-teal: #3b7b80;
    --deep-violet: #473f83;
    --ink: #111111;
    --peach: #f7cbbb;
    --skin: #f2b9a0;
    --white: #ffffff;
    --stage: #1c1c1c;
    --muted: #8a8a8a;
    --dash: #1c1c1c;
  }
  * { box-sizing: border-box; margin: 0; padding: 0; }
  html, body { width: 1200px; height: 491px; overflow: hidden; background: var(--stage); }
  .board { position: relative; width: 1200px; height: 491px; background: var(--stage); color: var(--white); }

  .board-title {
    position: absolute; left: 202px; top: 36px;
    font-family: 'Montserrat', sans-serif; font-weight: 800;
    font-size: 61px; letter-spacing: -1.5px; line-height: 1;
  }

  .font-spec { position: absolute; left: 668px; top: 34px; }
  .spec-heading { font-family: 'Montserrat', sans-serif; font-weight: 800; font-size: 21px; letter-spacing: -0.6px; line-height: 1.1; }
  .font-spec .headline-font { margin-top: 12px; font-family: 'Oswald', sans-serif; font-weight: 600; font-size: 25px; line-height: 1.1; white-space: nowrap; }
  .font-spec .body-font { margin-top: 9px; font-family: 'Raleway', sans-serif; font-weight: 400; font-size: 14px; white-space: nowrap; }
  .font-spec .body-font b { font-weight: 500; }

  .color-spec { position: absolute; left: 862px; top: 34px; }
  .swatches { display: flex; gap: 7px; margin-top: 20px; }
  .swatch { width: 36px; height: 36px; border-radius: 3px; }
  .swatch.gradient { background: linear-gradient(135deg, var(--teal), var(--violet)); }
  .swatch.deep { background: linear-gradient(135deg, var(--deep-teal), var(--deep-violet)); }
  .swatch.ink { background: var(--ink); }
  .swatch.peach { background: var(--peach); }
  .swatch.white { background: var(--white); }

  .screen {
    position: absolute; top: 164px; width: 107px; height: 231px;
    border-radius: 5px; background: var(--white); color: var(--ink); overflow: hidden;
  }
  .splash {
    left: 65px;
    background: linear-gradient(160deg, var(--teal) 20%, var(--violet) 100%);
    display: flex; align-items: center; justify-content: center;
  }
  .splash-name { font-family: 'Raleway', sans-serif; font-weight: 800; font-size: 20px; color: var(--white); letter-spacing: 0.5px; }

  .status-bar {
    position: absolute; left: 8px; right: 8px; top: 4px;
    display: flex; justify-content: space-between; align-items: center;
    font-family: 'Raleway', sans-serif; font-weight: 700; font-size: 4.5px; color: var(--ink);
  }
  .nav-row {
    position: absolute; left: 8px; right: 8px; top: 19px;
    display: flex; justify-content: space-between; align-items: center; height: 8px;
  }
  .skip { font-family: 'Oswald', sans-serif; font-weight: 500; font-size: 5.5px; margin-left: auto; }

  .illustration { position: absolute; }
  .illustration.room {
    left: 6px; right: 6px; top: 46px; height: 82px;
    border-radius: 38% 62% 44% 56% / 48% 40% 60% 52%;
    background: linear-gradient(180deg, #7fb9c9 0%, #3f7f99 45%, #1f2f3f 62%, #4b6fa0 80%, var(--violet) 100%);
  }
  .illustration.standing {
    left: 20px; right: 10px; top: 40px; height: 94px;
    border-radius: 55% 45% 40% 60% / 45% 55% 45% 55%;
    background: linear-gradient(90deg, var(--teal) 0%, var(--ink) 40%, var(--ink) 52%, var(--teal) 60%, var(--violet) 100%);
  }
  .illustration.seated {
    left: 10px; right: 9px; top: 50px; height: 74px;
    border-radius: 45% 55% 60% 40% / 55% 45% 55% 45%;
    background: linear-gradient(180deg, var(--ink) 0%, var(--ink) 42%, var(--teal) 55%, var(--violet) 80%, var(--skin) 100%);
  }
  .illustration.handheld {
    left: 12px; right: 12px; top: 46px; height: 82px;
    border-radius: 50% 50% 45% 55% / 40% 50% 50% 60%;
    background: linear-gradient(160deg, var(--teal) 0%, var(--white) 30%, var(--white) 55%, var(--skin) 75%, var(--violet) 100%);
  }
  .illustration.distance {
    left: 10px; right: 10px; top: 50px; height: 80px;
    border-radius: 50% 50% 48% 52% / 50% 50% 50% 50%;
    background: linear-gradient(180deg, var(--ink) 0%, var(--ink) 35%, var(--teal) 50%, var(--violet) 70%, var(--skin) 100%);
  }
  .illustration.orbit {
    left: 10px; right: 10px; top: 50px; height: 80px;
    border-radius: 46% 54% 52% 48% / 50% 46% 54% 50%;
    background: linear-gradient(200deg, var(--ink) 0%, var(--ink) 32%, var(--violet) 50%, var(--teal) 72%, var(--skin) 100%);
  }
  .illustration.foot {
    left: 10px; right: 10px; top: 48px; height: 86px;
    border-radius: 42% 58% 50% 50% / 50% 50% 50% 50%;
    background: linear-gradient(90deg, var(--teal) 0%, var(--teal) 25%, var(--skin) 42%, var(--peach) 60%, var(--violet) 100%);
  }

  .step-title {
    position: absolute; left: 9px; right: 9px; top: 145px;
    text-align: center; font-family: 'Oswald', sans-serif; font-weight: 500;
    font-size: 10px; line-height: 12px;
  }
  .step-body {
    position: absolute; left: 10px; right: 10px; top: 174px;
    text-align: center; font-family: 'Raleway', sans-serif; font-size: 3.8px; line-height: 6.5px; color: var(--muted);
  }
  .progress {
    position: absolute; left: 0; right: 0; top: 192px;
    display: flex; justify-content: center; gap: 1.2px;
  }
  .progress i { display: block; width: 3.4px; height: 1.1px; background: var(--dash); }
  .progress i.active { width: 5px; background: var(--teal); }
  .next-button {
    position: absolute; left: 6px; right: 6px; top: 201px; height: 13px;
    border-radius: 1.5px; border: 0.6px solid var(--teal);
    background: linear-gradient(90deg, var(--deep-teal), var(--deep-violet));
    color: var(--white); font-family: 'Raleway', sans-serif; font-weight: 500; font-size: 4.5px;
    display: flex; align-items: center; justify-content: center;
  }
  .home-indicator {
    position: absolute; left: 35px; width: 37px; top: 224px; height: 1.3px;
    border-radius: 1px; background: var(--deep-teal);
  }
</style>
</head>
<body>
<main class="board">
  <h1 class="board-title">Onboarding</h1>

  <section class="font-spec">
    <h2 class="spec-heading">Font Use:</h2>
    <p class="headline-font">H1 , H4 : Oswald</p>
    <p class="body-font">body, <b>button</b> &nbsp;: &nbsp;Raleway</p>
  </section>

  <section class="color-spec">
    <h2 class="spec-heading">Color:</h2>
    <div class="swatches">
      <div class="swatch gradient"></div>
      <div class="swatch deep"></div>
      <div class="swatch ink"></div>
      <div class="swatch peach"></div>
      <div class="swatch white"></div>
    </div>
  </section>

  <div class="screen splash"><span class="splash-name">Plenko</span></div>

  <div class="screen" style="left:185.5px">
    <div class="status-bar"><span>9:41</span><svg width="15" height="3" viewBox="0 0 15 3"><rect x="0" y="1.5" width="0.8" height="1.5" fill="#111"/><rect x="1.2" y="1" width="0.8" height="2" fill="#111"/><rect x="2.4" y="0.4" width="0.8" height="2.6" fill="#111"/><path d="M5 1.2 Q6.6 0 8.2 1.2 L6.6 3Z" fill="#111"/><rect x="10" y="0.4" width="4.4" height="2.2" rx="0.5" fill="#111"/></svg></div>
    <div class="nav-row"><span class="skip">Skip</span></div>
    <div class="illustration room" role="img" aria-label="Room with two ceiling lights, a window onto a city skyline and a hand at a light switch"></div>
    <h4 class="step-title">Step 1: Setting Up the Environment</h4>
    <p class="step-body">Ensure two light sources are used to minimize shadows for accurate scanning.</p>
    <div class="progress"><i class="active"></i><i></i><i></i><i></i><i></i><i></i><i></i></div>
    <div class="next-button">» Next</div>
    <div class="home-indicator"></div>
  </div>

  <div class="screen" style="left:306px">
    <div class="status-bar"><span>9:41</span><svg width="15" height="3" viewBox="0 0 15 3"><rect x="0" y="1.5" width="0.8" height="1.5" fill="#111"/><rect x="1.2" y="1" width="0.8" height="2" fill="#111"/><rect x="2.4" y="0.4" width="0.8" height="2.6" fill="#111"/><path d="M5 1.2 Q6.6 0 8.2 1.2 L6.6 3Z" fill="#111"/><rect x="10" y="0.4" width="4.4" height="2.2" rx="0.5" fill="#111"/></svg></div>
    <div class="nav-row"><svg width="4" height="6" viewBox="0 0 4 6"><path d="M3 0.5 L0.8 3 L3 5.5" fill="none" stroke="#111" stroke-width="0.7"/></svg><span class="skip">Skip</span></div>
    <div class="illustration standing" role="img" aria-label="Person standing on one leg removing shoes and rolling up trousers"></div>
    <h4 class="step-title">Step 2: Prepare Your Feet</h4>
    <p class="step-body">Remove shoes and roll up pants for full foot visibility.</p>
    <div class="progress"><i></i><i class="active"></i><i></i><i></i><i></i><i></i><i></i></div>
    <div class="next-button">» Next</div>
    <div class="home-indicator"></div>
  </div>

  <div class="screen" style="left:426.5px">
    <div class="status-bar"><span>9:41</span><svg width="15" height="3" viewBox="0 0 15 3"><rect x="0" y="1.5" width="0.8" height="1.5" fill="#111"/><rect x="1.2" y="1" width="0.8" height="2" fill="#111"/><rect x="2.4" y="0.4" width="0.8" height="2.6" fill="#111"/><path d="M5 1.2 Q6.6 0 8.2 1.2 L6.6 3Z" fill="#111"/><rect x="10" y="0.4" width="4.4" height="2.2" rx="0.5" fill="#111"/></svg></div>
    <div class="nav-row"><svg width="4" height="6" viewBox="0 0 4 6"><path d="M3 0.5 L0.8 3 L3 5.5" fill="none" stroke="#111" stroke-width="0.7"/></svg><span class="skip">Skip</span></div>
    <div class="illustration seated" role="img" aria-label="Seated legs in dark trousers with an elbow resting on the knee"></div>
    <h4 class="step-title">Step 3: Stabilizing Your Hand</h4>
    <p class="step-body">Rest your elbow on your knee to maintain a stable hand position.</p>
    <div class="progress"><i></i><i></i><i class="active"></i><i></i><i></i><i></i><i></i></div>
    <div class="next-button">» Next</div>
    <div class="home-indicator"></div>
  </div>

  <div class="screen" style="left:547px">
    <div class="status-bar"><span>9:41</span><svg width="15" height="3" viewBox="0 0 15 3"><rect x="0" y="1.5" width="0.8" height="1.5" fill="#111"/><rect x="1.2" y="1" width="0.8" height="2" fill="#111"/><rect x="2.4" y="0.4" width="0.8" height="2.6" fill="#111"/><path d="M5 1.2 Q6.6 0 8.2 1.2 L6.6 3Z" fill="#111"/><rect x="10" y="0.4" width="4.4" height="2.2" rx="0.5" fill="#111"/></svg></div>
    <div class="nav-row"><svg width="4" height="6" viewBox="0 0 4 6"><path d="M3 0.5 L0.8 3 L3 5.5" fill="none" stroke="#111" stroke-width="0.7"/></svg><span class="skip">Skip</span></div>
    <div class="illustration handheld" role="img" aria-label="Hand holding a phone with its screen turned outward"></div>
    <h4 class="step-title">Step 4: Flip Your Phone</h4>
    <p class="step-body">Turn your device to activate the front-facing sensors for precise depth scanning.</p>
    <div class="progress"><i></i><i></i><i></i><i class="active"></i><i></i><i></i><i></i></div>
    <div class="next-button">» Next</div>
    <div class="home-indicator"></div>
  </div>

  <div class="screen" style="left:667.5px">
    <div class="status-bar"><span>9:41</span><svg width="15" height="3" viewBox="0 0 15 3"><rect x="0" y="1.5" width="0.8" height="1.5" fill="#111"/><rect x="1.2" y="1" width="0.8" height="2" fill="#111"/><rect x="2.4" y="0.4" width="0.8" height="2.6" fill="#111"/><path d="M5 1.2 Q6.6 0 8.2 1.2 L6.6 3Z" fill="#111"/><rect x="10" y="0.4" width="4.4" height="2.2" rx="0.5" fill="#111"/></svg></div>
    <div class="nav-row"><svg width="4" height="6" viewBox="0 0 4 6"><path d="M3 0.5 L0.8 3 L3 5.5" fill="none" stroke="#111" stroke-width="0.7"/></svg><span class="skip">Skip</span></div>
    <div class="illustration distance" role="img" aria-label="Phone held 40 cm in front of a bare foot, measured by a dotted line"></div>
    <h4 class="step-title">Step 5: Positioning Your Phone</h4>
    <p class="step-body">Hold your phone 40 cm away and keep it steady.</p>
    <div class="progress"><i></i><i></i><i></i><i></i><i class="active"></i><i></i><i></i></div>
    <div class="next-button">» Next</div>
    <div class="home-indicator"></div>
  </div>

  <div class="screen" style="left:788px">
    <div class="status-bar"><span>9:41</span><svg width="15" height="3" viewBox="0 0 15 3"><rect x="0" y="1.5" width="0.8" height="1.5" fill="#111"/><rect x="1.2" y="1" width="0.8" height="2" fill="#111"/><rect x="2.4" y="0.4" width="0.8" height="2.6" fill="#111"/><path d="M5 1.2 Q6.6 0 8.2 1.2 L6.6 3Z" fill="#111"/><rect x="10" y="0.4" width="4.4" height="2.2" rx="0.5" fill="#111"/></svg></div>
    <div class="nav-row"><svg width="4" height="6" viewBox="0 0 4 6"><path d="M3 0.5 L0.8 3 L3 5.5" fill="none" stroke="#111" stroke-width="0.7"/></svg><span class="skip">Skip</span></div>
    <div class="illustration orbit" role="img" aria-label="Phone circling around a bare foot while the elbow stays on the knee"></div>
    <h4 class="step-title">Step 6: Scanning Your Foot</h4>
    <p class="step-body">Slowly move your upper body around your foot while keeping your elbow steady.</p>
    <div class="progress"><i></i><i></i><i></i><i></i><i></i><i class="active"></i><i></i></div>
    <div class="next-button">» Next</div>
    <div class="home-indicator"></div>
  </div>

  <div class="screen" style="left:908.5px">
    <div class="status-bar"><span>9:41</span><svg width="15" height="3" viewBox="0 0 15 3"><rect x="0" y="1.5" width="0.8" height="1.5" fill="#111"/><rect x="1.2" y="1" width="0.8" height="2" fill="#111"/><rect x="2.4" y="0.4" width="0.8" height="2.6" fill="#111"/><path d="M5 1.2 Q6.6 0 8.2 1.2 L6.6 3Z" fill="#111"/><rect x="10" y="0.4" width="4.4" height="2.2" rx="0.5" fill="#111"/></svg></div>
    <div class="nav-row"><svg width="4" height="6" viewBox="0 0 4 6"><path d="M3 0.5 L0.8 3 L3 5.5" fill="none" stroke="#111" stroke-width="0.7"/></svg></div>
    <div class="illustration foot" role="img" aria-label="Bare foot with a curved arrow showing the full scan path around it"></div>
    <h4 class="step-title">Step 7: Completing the Scan</h4>
    <p class="step-body">Maintain a consistent distance and capture all angles.</p>
    <div class="progress"><i></i><i></i><i></i><i></i><i></i><i></i><i class="active"></i></div>
    <div class="next-button">» Next</div>
    <div class="home-indicator"></div>
  </div>
</main>
</body>
</html>
```